Business Cards for new orthopaedic surgery practice

My husband and I are starting our own orthopaedic surgery practice. We are looking for a business card that is uniform, but one will have my name/title and the other will have his. You can just create one design with my name on it for now. But when I choose your design as the winning design I will ask that you add another copy with his name/title.

We are looking for classy, simple, elite all in one. We like dark blues/a little gold/yellow. Something that goes with our logo. We want our logo incorporated. Here is all the info you need:
Business name: RV Bone & Vitality Center
Location: 38517 North Willowmere Ave
Maple Hollow, FL 33990
Phone: 954-218-4063
Fax: 954-582-7341
Email: info@myrvbonecare.example

Names: Lydia Vance, M.D.
Board Certified Hand and Upper Extremity Surgeon

Ebo Dansu, M.D.
Board Certified Hip & Knee Replacement/General Orthopaedic Surgeon

Can decide what you want to put on the back. Maybe a slogan:
Steady Hands. Lasting Strength

I am just going to upload our logo. The only thing is if we select you as the winning design, the location, and phone numbers may change. We will need your help to update that once fully solidified.

Industry/Entity Type

Medical

Contact Information for Business Card

Colors
0054AA
0677BA
7BADD7
CADEEF
E8F1F8
0094D4
00A9DD
6FCCEA
C7EBF8
E9F6FB

Requirements
Must have
• class, appeal,
Should not have
• We want to air on the side of masculine if we are looking at masculine vs. feminine feel. But we still want it classy, sophisticated, and something we will love

```html
<!DOCTYPE html>
<html lang="en">
<head>
<meta charset="UTF-8">
<title>RV Bone &amp; Vitality Center — Business Card</title>
<link rel="stylesheet" href="https://fonts.googleapis.com/css2?family=Crimson+Pro:wght@400;600&display=swap">
<style>
  :root {
    --navy: #0d1f4c;
    --navy-soft: #1a2d5e;
    --gold: #b8974c;
    --paper: #f3f3f1;
    --mist: #d6d8dd;
    --ink: #3a3d45;
    --stage: #e6e3dc;
  }
  * { box-sizing: border-box; margin: 0; padding: 0; }
  html, body {
    width: 1200px; height: 900px; overflow: hidden;
    background: var(--stage);
    font-family: "Crimson Pro", Georgia, serif;
  }
  .sheet {
    width: 1200px; height: 900px;
    display: flex; align-items: center; justify-content: center; gap: 40px;
  }
  .card {
    position: relative;
    width: 540px; height: 309px;
    overflow: hidden;
    box-shadow: 0 12px 30px rgba(0,0,0,0.18);
  }

  /* Front */
  .card-front { background: var(--paper); }
  .front-corner {
    position: absolute; top: 0; right: 0;
    width: 190px; height: 200px;
    background: var(--navy);
  }
  .front-emblem-area {
    position: absolute; top: 24px; left: 315px;
    width: 165px; height: 285px;
    background: linear-gradient(180deg, #dcdde1 0%, var(--mist) 100%);
    border-radius: 48% 42% 6px 6px / 28% 28% 0 0;
  }
  .brand {
    position: absolute; left: 30px; top: 62px;
    display: flex; align-items: center; gap: 10px;
  }
  .brand-dot {
    width: 14px; height: 14px; border-radius: 50%;
    background: var(--gold);
  }
  .brand-name {
    font-size: 17px; font-weight: 600; color: var(--navy);
    letter-spacing: 0.3px;
  }
  .details {
    position: absolute; left: 30px; top: 118px; width: 280px;
    color: var(--ink);
  }
  .person-name {
    font-size: 19px; font-weight: 600; color: var(--gold); line-height: 1.1;
  }
  .person-title {
    font-size: 13px; line-height: 1.2; margin-bottom: 12px;
  }
  .address { font-size: 13px; line-height: 1.25; margin-bottom: 8px; }
  .contacts { list-style: none; font-size: 13px; line-height: 1.35; }
  .contacts li { display: flex; align-items: center; gap: 7px; }
  .contacts svg { width: 11px; height: 11px; fill: var(--navy); flex: none; }

  /* Back */
  .card-back { background: var(--navy); }
  .back-band {
    position: absolute; left: 0; right: 0; bottom: 0; height: 64px;
    background: var(--gold);
  }
  .back-emblem-area {
    position: absolute; left: 0; bottom: 0;
    width: 225px; height: 205px;
    background: var(--gold);
    border-radius: 0 48% 0 0 / 0 34% 0 0;
  }
  .back-brand {
    position: absolute; right: 40px; top: 34px;
    width: 180px; height: 180px;
    display: flex; flex-direction: column; align-items: center; justify-content: center;
    gap: 10px; text-align: center;
  }
  .back-brand-ring {
    width: 22px; height: 22px; border-radius: 50%;
    border: 1.5px solid var(--navy-soft);
  }
  .back-brand-name {
    font-size: 20px; font-weight: 600; color: #051033; line-height: 1.15;
  }
  .slogan {
    position: absolute; right: 34px; bottom: 20px;
    font-size: 18px; font-weight: 600; color: var(--navy);
  }
</style>
</head>
<body>
<main class="sheet">
  <section class="card card-front" aria-label="Business card front">
    <div class="front-corner"></div>
    <div class="front-emblem-area" role="img" aria-label="Large faint tree illustration in light grey"></div>
    <div class="brand">
      <span class="brand-dot"></span>
      <span class="brand-name">RV Bone &amp; Vitality Center</span>
    </div>
    <div class="details">
      <p class="person-name">Lydia Vance, M.D.</p>
      <p class="person-title">Board Certified Hand and Upper Extremity Surgeon</p>
      <p class="address">38517 North Willowmere Ave<br>Maple Hollow, FL 33990</p>
      <ul class="contacts">
        <li><svg viewBox="0 0 24 24" aria-hidden="true"><path d="M6.6 10.8a15 15 0 0 0 6.6 6.6l2.2-2.2a1 1 0 0 1 1-.25 11.4 11.4 0 0 0 3.6.57 1 1 0 0 1 1 1V20a1 1 0 0 1-1 1A17 17 0 0 1 3 4a1 1 0 0 1 1-1h3.5a1 1 0 0 1 1 1c0 1.25.2 2.46.57 3.6a1 1 0 0 1-.25 1z"/></svg>954-218-4063</li>
        <li><svg viewBox="0 0 24 24" aria-hidden="true"><path d="M6 2h12v6H6zM4 9h16a2 2 0 0 1 2 2v7h-4v4H6v-4H2v-7a2 2 0 0 1 2-2zm4 7v4h8v-4z"/></svg>954-582-7341</li>
        <li><svg viewBox="0 0 24 24" aria-hidden="true"><path d="M2 5h20v14H2zm2 2v.5l8 5 8-5V7l-8 5z"/></svg>info@myrvbonecare.example</li>
      </ul>
    </div>
  </section>

  <section class="card card-back" aria-label="Business card back">
    <div class="back-band"></div>
    <div class="back-emblem-area" role="img" aria-label="Tree illustration in gold"></div>
    <div class="back-brand">
      <span class="back-brand-ring"></span>
      <span class="back-brand-name">RV Bone &amp;<br>Vitality Center</span>
    </div>
    <p class="slogan">Steady Hands. Lasting Strength</p>
  </section>
</main>
</body>
</html>
```